Bottle label design for 4 litre jug

Need to create a label for my chemical products please attached label. Must have the side labels, colors must be complimented with logo attached. Come up with a clean yet high end product look to it. the brand name is Varnon Glass cleaner, Trelby Shine Works is the logo,
Redisgn with new updated look, there are a total of 8 labels to be made for oterh products.

Industry/Entity Type

Cleaning industry

Font styles to use
Serif
Other font styles liked:
• Lora Bold, EB garamond, or use any font you choose, clean and bold

Colors
0054AA
0677BA
7BADD7
CADEEF
E8F1F8
0094D4
00A9DD
6FCCEA
C7EBF8
E9F6FB
00AB8E
00BBA5
67D7C9
C6EFE9
E9F9F6

```html
<!DOCTYPE html>
<html lang="en">
<head>
<meta charset="utf-8">
<title>Varnon Glass Cleaner – 4 L Label</title>
<link rel="stylesheet" href="https://fonts.googleapis.com/css2?family=EB+Garamond:ital,wght@0,400;0,600;0,700;1,400;1,600&family=Lora:ital,wght@0,600;0,700;1,600&display=swap">
<style>
  :root{
    --blue-900:#0054aa;
    --blue-700:#0677ba;
    --blue-400:#7badd7;
    --blue-200:#cadeef;
    --blue-50:#e8f1f8;
    --cyan-700:#0094d4;
    --cyan-600:#00a9dd;
    --cyan-400:#6fccea;
    --cyan-200:#c7ebf8;
    --cyan-50:#e9f6fb;
    --teal-700:#00ab8e;
    --teal-600:#00bba5;
    --teal-400:#67d7c9;
    --teal-200:#c6efe9;
    --teal-50:#e9f9f6;
    --ink:#0b2e52;
    --white:#ffffff;
  }
  *{box-sizing:border-box;margin:0;padding:0}
  html,body{width:1200px;height:675px;overflow:hidden;background:var(--white)}
  .canvas{position:relative;width:1200px;height:675px;background:var(--white);font-family:"EB Garamond",serif;color:var(--ink)}

  .side-panel{position:absolute;top:87px;width:232px;height:506px;border-radius:16px;
    background:linear-gradient(180deg,var(--cyan-50) 0%,var(--cyan-200) 100%);
    border:3px solid var(--cyan-700)}
  .side-panel--left{left:91px;padding:12px 11px}
  .side-panel--right{left:885px;padding:16px 13px 14px;display:flex;flex-direction:column;justify-content:space-between}

  .safety__title{font-family:"Lora",serif;font-weight:700;font-size:20px;text-align:center;letter-spacing:1px;line-height:1;color:var(--blue-900);margin-bottom:6px}
  .safety__text{font-size:8.3px;line-height:10.6px;text-align:justify}
  .safety__text b{font-weight:700;color:var(--blue-900)}
  .safety__text--fr{margin-top:6px}
  .safety__note{font-style:italic;font-size:8.3px;line-height:11px;margin-top:3px}
  .hazard{display:block;margin:4px auto 0;width:66px;height:66px}
  .maker{position:absolute;left:0;right:0;bottom:10px;text-align:center;font-style:normal;font-family:"Lora",serif;font-weight:700;font-size:11px;line-height:15px;color:var(--blue-900)}

  .front{position:absolute;left:331px;top:87px;width:546px;height:506px;overflow:hidden;border-radius:0 16px 0 0;
    background:radial-gradient(ellipse at 50% 38%,var(--cyan-600) 0%,var(--blue-700) 38%,var(--blue-900) 80%)}
  .front__seal{position:absolute;left:-40px;top:-50px;width:138px;height:138px;border-radius:50%;background:var(--teal-700)}
  .maker-mark{position:absolute;left:0;right:0;top:46px;display:flex;justify-content:center;align-items:center;gap:9px}
  .maker-mark__dot{width:22px;height:22px;border-radius:50%;background:var(--teal-600)}
  .maker-mark__name{font-family:"Lora",serif;font-weight:600;font-size:21px;color:var(--white);letter-spacing:.5px}
  .product{position:absolute;left:0;right:0;top:140px;transform:rotate(-5deg);text-align:center}
  .product__name{font-family:"Lora",serif;font-weight:700;font-size:96px;line-height:1;color:var(--white);letter-spacing:3px;
    text-shadow:3px 4px 0 var(--blue-900)}
  .product__type{font-family:"Lora",serif;font-weight:700;font-size:34px;line-height:1;color:var(--cyan-200);letter-spacing:5px;margin-top:6px}
  .product__rule{display:block;width:250px;height:2px;margin:12px auto 0;background:var(--teal-400)}
  .product__claim{font-family:"Lora",serif;font-style:italic;font-weight:600;font-size:12.5px;line-height:17px;color:var(--white);margin-top:9px}
  .front__wave{position:absolute;left:0;bottom:0;width:546px;height:200px}
  .volume{position:absolute;left:0;top:422px;width:112px;height:49px}
  .volume__text{position:absolute;left:22px;top:428px;font-family:"Lora",serif;font-weight:700;font-size:30px;line-height:36px;color:var(--white);letter-spacing:2px}
  .benefits{position:absolute;right:45px;top:402px;list-style:none;text-align:right;font-weight:600;font-size:22px;line-height:25px;color:var(--blue-900)}

  .use__lead{font-style:italic;font-size:13.2px;line-height:16.5px;text-align:justify}
  .use__lead b{font-style:normal;font-weight:700;color:var(--blue-900)}
  .use__body{font-size:13.6px;line-height:17px;text-align:justify}
  .use__body i{font-style:italic}
  .use__flag{font-family:"Lora",serif;font-weight:700;font-size:11.5px;text-align:center;letter-spacing:.4px;color:var(--blue-900)}
</style>
</head>
<body>
<main class="canvas">

  <section class="side-panel side-panel--left">
    <h2 class="safety__title">GLASS CLEAN</h2>
    <p class="safety__text"><b>WARNING:</b> Causes eye irritation. Prolonged or repeated skin contact may cause irritation.
      <b>PRECAUTIONS:</b> Wash hands thoroughly after handling. Wear protective gloves/eye protection/face protection. Do not eat, drink, or smoke when using this product.
      <b>FIRST AID:</b> IF IN EYES: Rinse cautiously with water for several minutes. Remove contact lenses, if present and easy to do. Continue rinsing. If eye irritation persists: get medical attention/advice. IF SWALLOWED: Rinse mouth. DO NOT induce vomiting. Drink large quantities of water. Call a POISON CENTER or doctor/physician if you feel unwell. If skin irritation occurs: Get medical advice/attention.</p>
    <p class="safety__note">See Safety Data Sheet.</p>
    <svg class="hazard" viewBox="0 0 68 68" role="img" aria-label="Exclamation mark hazard pictogram">
      <rect x="14" y="14" width="40" height="40" transform="rotate(45 34 34)" fill="none" stroke="#0b2e52" stroke-width="4"/>
      <path d="M30.5 18h7l-1.3 24h-4.4z" fill="#0b2e52"/>
      <circle cx="34" cy="48" r="3.6" fill="#0b2e52"/>
    </svg>
    <p class="safety__text safety__text--fr"><b>ATTENTION:</b> Provoque une irritation oculaire. Un contact cutané prolongé ou répété peut provoquer une irritation.
      <b>PRÉCAUTIONS:</b> Se laver soigneusement après la manipulation. Porter des gants de protection/protection des yeux/protection du visage. Ne pas manger, boire ou fumer lors de l'utilisation de ce produit.
      <b>PREMIER SOINS:</b> EN CAS DE CONTACT AVEC LES YEUX: Rincer avec précaution à l'eau pendant plusieurs minutes. Enlevez les lentilles de contact si la victime en porte et si elles peuvent être facilement enlevées. Continuer à rinçage. Si l'irritation des yeux persiste: consulter un médecin. EN CAS D'INGESTION: Rincer la bouche. NE PAS faire vomir. Buvez de grandes quantités d'eau. Appelez un CENTRE ANTIPOISON/un médecin en cas de malaise. En cas d'irritation cutanée: Consulter un médecin.</p>
    <p class="safety__note">Consulter la fiche de données de sécurité.</p>
    <address class="maker">TRELBY SHINE WORKS<br>Brantwell, Ontario K2R 4P8</address>
  </section>

  <section class="front">
    <div class="front__seal" role="img" aria-label="Eco certification seal"></div>
    <div class="maker-mark"><span class="maker-mark__dot"></span><span class="maker-mark__name">Trelby Shine Works</span></div>
    <div class="product">
      <h1 class="product__name">VARNON</h1>
      <p class="product__type">GLASS CLEANER</p>
      <span class="product__rule"></span>
      <p class="product__claim">Dries fast without leaving a film or streaking.<br>Polishes as it dissolves dirt and dingy film.</p>
    </div>
    <svg class="front__wave" viewBox="0 0 546 200" preserveAspectRatio="none" aria-hidden="true">
      <defs>
        <linearGradient id="wave-fill" x1="0" y1="0" x2="0" y2="1">
          <stop offset="0" stop-color="#c7ebf8"/><stop offset="1" stop-color="#e9f6fb"/>
        </linearGradient>
      </defs>
      <path d="M0 90 C150 60 330 80 546 0 L546 200 L0 200Z" fill="#67d7c9"/>
      <path d="M0 86 C150 52 330 70 546 -6 L546 18 C330 88 150 66 0 94Z" fill="#ffffff"/>
      <path d="M0 98 C150 70 330 88 546 18 L546 200 L0 200Z" fill="url(#wave-fill)"/>
    </svg>
    <svg class="volume" viewBox="0 0 112 49" aria-hidden="true"><path d="M0 0H112L96 24.5 112 49H0Z" fill="#00ab8e"/></svg>
    <span class="volume__text">4 L</span>
    <ul class="benefits">
      <li>Non Corrosive</li>
      <li>Low Carbon Footprint</li>
      <li>Completely Biodegradeable</li>
    </ul>
  </section>

  <section class="side-panel side-panel--right">
    <p class="use__lead">Read entire label before using. For industrial and institutional use only. <b>Keep out of reach of children.</b></p>
    <p class="use__body"><i>For windows, glass, mirrors, windshields, ceramic tile, porcelain, etc.</i> Use full strength. Spray on and wipe off with a clean towel or cloth.</p>
    <p class="use__flag">NOT AFFECTED BY FREEZING.</p>
    <p class="use__lead">Lire l'étiquette au complet avant d'utiliser le produit. Pour usage industriel ou dans un établissement seulement. <b>Garder hors de la portée des enfants.</b></p>
    <p class="use__body"><i>Pour vitres, miroirs, carreaux en céramique, verre, porcelaine, etc.</i> Ne pas diluer. Vaporiser et essuyer à l'aide d'un chiffon propre.</p>
    <p class="use__flag">NE CRAINT PAS LE GEL.</p>
  </section>

</main>
</body>
</html>
```